co working space / serviced office/ business centre

Brevlo - brevlo.in, is a very young brand bieng run by 3 young entrepreneurs. We want to be become out of the league company delivering fabulous and beautiful serviced offices in India and abroad. We hire designers who have made spaces across the world. We want to get visiting card design which gives complete fresh look to the people who carries that card, has to be very impactful and should symbolise happy young and energetic brand. should be completely out of the box thinking of international level, should portray global brand image.

Target Market(s)

Startups, (Small, medium and large corporates)

Industry/Entity Type

Business

Contact Information for Business Card

Name, Email, Address, Mobile number, Landline number, website

Colors

Designer to choose colors to be used in the design.

Requirements
Must have
• Nice new shape
Nice to have
• We want creative cuts, different size and impactful brand clarity
Should not have
• Boring and regular design and shape

```html
<!DOCTYPE html>
<html lang="en">
<head>
<meta charset="utf-8">
<title>Brevlo business card</title>
<link rel="stylesheet" href="https://fonts.googleapis.com/css2?family=Work+Sans:wght@400;500;600&display=swap">
<style>
  :root {
    --red: #e8202a;
    --ink: #161616;
    --paper: #ffffff;
    --stage: #e9e6e1;
    --muted: #f2f2f2;
  }
  * { margin: 0; padding: 0; box-sizing: border-box; }
  html, body { width: 1200px; height: 930px; overflow: hidden; }
  body { background: var(--stage); font-family: "Work Sans", sans-serif; position: relative; }

  .card {
    position: absolute; left: 278px; width: 645px; height: 369px;
    border-radius: 24px; overflow: hidden;
    box-shadow: 0 8px 24px rgba(0,0,0,.18);
  }
  .card--front { top: 75px; background: var(--ink); }
  .card--back { top: 486px; background: var(--ink); }

  .front-brand {
    position: absolute; left: 0; top: 0; width: 336px; height: 100%;
    background: var(--paper);
  }
  .front-notch { position: absolute; left: 336px; top: 79px; }

  .brand { position: absolute; text-align: center; color: var(--red); }
  .brand__name { font-weight: 600; letter-spacing: 3px; line-height: 1; white-space: nowrap; }
  .brand__mark { display: inline-block; border-radius: 50%; background: var(--red); vertical-align: middle; }
  .brand__tagline { font-weight: 500; letter-spacing: 1px; white-space: nowrap; }

  .card--front .brand { left: 28px; width: 280px; top: 140px; }
  .card--front .brand__name { font-size: 46px; }
  .card--front .brand__mark { width: 16px; height: 16px; margin-right: 10px; margin-top: -8px; }
  .card--front .brand__tagline { font-size: 15px; margin-top: 14px; }

  .card--back .brand { left: 122px; width: 400px; top: 112px; }
  .card--back .brand__name { font-size: 66px; }
  .card--back .brand__mark { width: 22px; height: 22px; margin-right: 14px; margin-top: -12px; }
  .card--back .brand__tagline { font-size: 20px; margin-top: 18px; }

  .contact { position: absolute; left: 384px; top: 78px; color: var(--muted); }
  .contact__name { color: var(--red); font-weight: 500; font-size: 32px; letter-spacing: .5px; line-height: 1; white-space: nowrap; }
  .contact__role { font-size: 15px; margin-top: 3px; }
  .contact__divider { width: 26px; height: 1px; background: var(--red); margin: 14px 0 12px; }
  .contact__address { font-size: 16px; line-height: 21px; }
  .contact__list { list-style: none; }
  .contact__list li { font-size: 16px; line-height: 20px; display: flex; align-items: center; }
  .contact__icon { width: 10px; height: 10px; margin-right: 12px; flex: none; }
</style>
</head>
<body>
  <section class="card card--front">
    <div class="front-brand"></div>
    <svg class="front-notch" width="28" height="40" viewBox="0 0 28 40"><path d="M0 0 L28 20 L0 40 Z" fill="#ffffff"/></svg>

    <div class="brand">
      <div class="brand__name"><span class="brand__mark"></span>BREVLO</div>
      <div class="brand__tagline">Plug in. Settle in.</div>
    </div>

    <div class="contact">
      <h1 class="contact__name">ARUN MEHRA</h1>
      <p class="contact__role">Director</p>
      <div class="contact__divider"></div>
      <p class="contact__address">48 Linden Park Road<br>Pune, MH 411001</p>
      <div class="contact__divider"></div>
      <ul class="contact__list">
        <li><svg class="contact__icon" viewBox="0 0 10 10"><path d="M2 0.5 L3.5 3 L2.6 4 Q4 6.5 6 7.4 L7 6.5 L9.5 8 L8.5 9.5 Q3 9 0.5 1.5 Z" fill="none" stroke="#e8202a" stroke-width="0.9"/></svg>020 4127 8830</li>
        <li><svg class="contact__icon" viewBox="0 0 10 10"><rect x="2.5" y="0.5" width="5" height="9" rx="0.8" fill="none" stroke="#e8202a" stroke-width="1"/><circle cx="5" cy="8" r="0.6" fill="#e8202a"/></svg>98220 41573</li>
        <li><svg class="contact__icon" viewBox="0 0 10 10"><rect x="0.5" y="2" width="9" height="6" fill="none" stroke="#e8202a" stroke-width="1"/><path d="M0.5 2 L5 5.5 L9.5 2" fill="none" stroke="#e8202a" stroke-width="1"/></svg>info@brevlo.in</li>
        <li><svg class="contact__icon" viewBox="0 0 10 10"><circle cx="5" cy="5" r="4.4" fill="none" stroke="#e8202a" stroke-width="0.9"/><ellipse cx="5" cy="5" rx="2" ry="4.4" fill="none" stroke="#e8202a" stroke-width="0.8"/><path d="M0.6 5 H9.4" stroke="#e8202a" stroke-width="0.8"/></svg>www.brevlo.in</li>
      </ul>
    </div>
  </section>

  <section class="card card--back">
    <div class="brand">
      <div class="brand__name"><span class="brand__mark"></span>BREVLO</div>
      <div class="brand__tagline">Plug in. Settle in.</div>
    </div>
  </section>
</body>
</html>
```